Hollendorf Business Card

This is the personal business card for Dr Mark Hollendorf and convers three area of his professional activity - all of them involve (foreign) languages:
o QRVB International Ltd - A translation company with 50 staff. Trades internationally
o WideHarbor Ltd - a global online auction marketplace for translation services (startup)
o Tonal Mosaic - cutting edge technology from the brain sciences which helps learners assimilate the sound patterns of a new language (startup)

Target Market(s)

The card needs to have a "cutting edge" feel - but for a fairly conservative audience - academics, investors.

Industry/Entity Type

Business

Requirements
Must have
• Text:
Dr Mark Hollendorf

Co-founder QRVB International Ltd (Language translation)
Founder WideHarbor Ltd (Translation marketplace)
Founder Tonal Mosaic (Language acquisition)

email: mark.oswin@velmora.co.nz
Phone: +64 21 596 3172
Twitter: @MarkOswin7

```html
<!DOCTYPE html>
<html lang="en">
<head>
<meta charset="utf-8">
<title>Hollendorf Business Card</title>
<link rel="stylesheet" href="https://fonts.googleapis.com/css2?family=Pinyon+Script&family=Tinos:wght@400;700&display=swap">
<style>
  :root {
    --paper: #ffffff;
    --olive: #9a9b6c;
    --olive-soft: #b9ba92;
    --maroon: #4a0c0c;
    --maroon-bright: #6e1414;
    --ink: #1a0505;
  }
  * { margin: 0; padding: 0; box-sizing: border-box; }
  html, body { width: 1200px; height: 686px; overflow: hidden; background: var(--paper); }
  .card {
    position: relative;
    width: 1200px;
    height: 686px;
    background: var(--paper);
    font-family: "Tinos", "Times New Roman", serif;
    overflow: hidden;
  }
  .corner-ornament, .center-ornament { position: absolute; display: block; }
  .corner-ornament--tl { left: 0; top: 0; }
  .corner-ornament--tr { right: 0; top: 0; }
  .corner-ornament--bl { left: 0; bottom: 0; }
  .corner-ornament--br { right: 0; bottom: 0; }
  .center-ornament { left: 490px; top: 172px; }

  .signature {
    position: absolute;
    top: 88px;
    left: 0;
    width: 1212px;
    text-align: center;
    font-family: "Pinyon Script", cursive;
    font-size: 26px;
    color: var(--ink);
  }
  .full-name {
    position: absolute;
    top: 296px;
    left: 0;
    width: 1212px;
    text-align: center;
    font-size: 20px;
    color: var(--maroon);
  }
  .profession {
    position: absolute;
    top: 352px;
    left: 0;
    width: 1212px;
    text-align: center;
    font-size: 18px;
    color: var(--ink);
  }
  .ventures {
    position: absolute;
    left: 201px;
    top: 462px;
    width: 360px;
    list-style: none;
    font-size: 15px;
    line-height: 19px;
    font-weight: 700;
    color: var(--maroon);
  }
  .ventures li { margin-bottom: 26px; }
  .ventures li:last-child { margin-bottom: 0; }
  .contact {
    position: absolute;
    left: 633px;
    top: 470px;
    font-size: 26px;
    line-height: 32px;
    color: var(--maroon-bright);
  }
</style>
</head>
<body>
<div class="card">
  <svg class="corner-ornament corner-ornament--tl" width="275" height="250" viewBox="0 0 275 250" role="img" aria-label="Olive ornamental corner flourish">
    <path d="M0 0H275V40H45V250H0Z" fill="var(--olive)" opacity="0.75"/>
  </svg>
  <svg class="corner-ornament corner-ornament--tr" width="320" height="250" viewBox="0 0 320 250" role="img" aria-label="Olive ornamental corner flourish">
    <path d="M0 0H320V250H275V40H0Z" fill="var(--olive)" opacity="0.75"/>
  </svg>
  <svg class="corner-ornament corner-ornament--bl" width="265" height="320" viewBox="0 0 265 320" role="img" aria-label="Olive ornamental corner flourish">
    <path d="M0 0H45V280H265V320H0Z" fill="var(--olive)" opacity="0.75"/>
  </svg>
  <svg class="corner-ornament corner-ornament--br" width="240" height="310" viewBox="0 0 240 310" role="img" aria-label="Olive ornamental corner flourish">
    <path d="M195 0H240V310H0V270H195Z" fill="var(--olive)" opacity="0.75"/>
  </svg>
  <svg class="center-ornament" width="220" height="115" viewBox="0 0 220 115" role="img" aria-label="Olive ornamental flourish divider">
    <defs>
      <radialGradient id="flourishTone" cx="50%" cy="35%" r="60%">
        <stop offset="0%" stop-color="var(--olive)"/>
        <stop offset="100%" stop-color="var(--olive-soft)"/>
      </radialGradient>
    </defs>
    <path d="M0 8H220V20H150L110 115L70 20H0Z" fill="url(#flourishTone)" opacity="0.8"/>
  </svg>

  <p class="signature">Dr. Mark Hollendorf</p>
  <p class="full-name">Mark Hollendorf</p>
  <p class="profession">Profession in Foreign Languages</p>

  <ul class="ventures">
    <li>Co-founder QRVB International Ltd<br>(Language Translation)</li>
    <li>Founder WideHarbor Ltd (Translation<br>Marketplace)</li>
    <li>Founder Tonal Mosaic (Language<br>acquisition)</li>
  </ul>

  <div class="contact">
    <p>Phone: +64 21 596 3172</p>
    <p>Twitter: @MarkOswin7</p>
    <p>E-mail: mark.oswin@velmora.co.nz</p>
  </div>
</div>
</body>
</html>
```